Norvane Website Design (New Start Up Investment Management Firm)

We need a website designed. We have attached a Powerpoint with our proposed website content (which is quite minimal), the format is just a suggestion but we would like to see your alternative and improved ideas. We are a boutique investment firm so are looking for something sleek and professional. I have included on the last page of the attachment our brand colours and font styles as well as attaching our logo design. We would like the successful designer to design the website and build the buttons etc.

On the "Contact Us" page, we are open to suggestions on how best to show the map, whether is should be static or open a google maps page. We would like the phone number and email address to be set up so people can click on them on their phone and it calls us or emails us directly.

We would prefer not to have photos of landscapes on the site.
Our website is hosted on a Linux based website.

We would also like 3 links at the bottom of each page for links to pdfs:
- Disclaimer, Terms and Conditions of Web Site Use
- Stewardship
- Pillar III

Target Market(s)

Institutional Investors

Industry/Entity Type

Investment

Coding

Coded - Design and coding required

Number of Pages Required

3 page

Font styles to use
Other font styles liked:
• Logo: Lato, Text: Source Sans Pro

Colors

Designer to choose colors to be used in the design.

Requirements
Must have
• The website must use the colours and fonts on the last page of the attached powerpoint. I can't see an option to select the exact colour palette below so please look at the PPT.
• For others please see Project description.
Should not have
• Landscape photos

```html
<!DOCTYPE html>
<html lang="en">
<head>
<meta charset="utf-8">
<title>Norvane Investment Management</title>
<link href="https://fonts.googleapis.com/css2?family=Lato:wght@400;700&display=swap" rel="stylesheet">
<style>
:root{
  --navy:#0b2f6b;
  --navy-deep:#0a2250;
  --ink:#1f2d4a;
  --text-light:#ffffff;
  --footer-bg:#f5f6f8;
  --footer-text:#2c3443;
  --border:#d6d9de;
  --muted:#9aa1ab;
}
*{box-sizing:border-box;margin:0;padding:0}
html,body{width:1200px;height:686px;overflow:hidden}
body{font-family:'Lato',sans-serif;background:#fff;color:var(--ink);position:relative}

.site-header{position:absolute;left:0;top:0;width:1200px;height:86px;background:#fff}
.brand{position:absolute;left:132px;top:24px;display:flex;align-items:center;gap:10px}
.brand-square{width:38px;height:38px;background:var(--navy)}
.brand-name{font-size:34px;font-weight:700;color:var(--navy);letter-spacing:1px;line-height:1}
.search{position:absolute;left:766px;top:30px;width:224px;height:32px;border:1px solid var(--border);border-radius:16px;display:flex;align-items:center;padding:0 12px 0 16px;font-size:12px;color:var(--muted)}
.search svg{margin-left:auto}
.login{position:absolute;left:996px;top:30px;width:72px;height:31px;border-radius:16px;background:var(--navy);color:#fff;font-size:13px;font-weight:700;display:flex;align-items:center;justify-content:center}
.header-rule{position:absolute;left:0;top:86px;width:1200px;height:4px;background:var(--navy)}

.hero{position:absolute;left:0;top:90px;width:1200px;height:508px;
  background:linear-gradient(100deg,#3b4a66 0%,#2a3a5c 35%,#1f2f55 65%,#34426a 100%)}
.hero-shade{position:absolute;inset:0;background:rgba(12,28,66,.45)}

.menu{position:absolute;left:132px;top:245px;display:flex;flex-direction:column;gap:17px}
.menu-item{display:flex;height:55px}
.menu-icon{width:76px;height:55px;background:var(--navy);display:flex;align-items:center;justify-content:center}
.menu-label{position:relative;width:158px;height:55px;background:#fff;display:flex;align-items:center;padding-left:19px;font-size:16px;font-weight:700;color:var(--navy);line-height:1.2}
.menu-label::after{content:"";position:absolute;left:158px;top:0;border-top:27.5px solid transparent;border-bottom:27.5px solid transparent;border-left:26px solid #fff}

.intro{position:absolute;left:444px;top:237px;width:630px;color:var(--text-light)}
.intro h1{font-size:21px;font-weight:400;line-height:30px}
.intro p{margin-top:10px;font-size:14px;line-height:28px}

.site-footer{position:absolute;left:0;top:598px;width:1200px;height:88px;background:var(--footer-bg);color:var(--footer-text);font-size:13px}
.footer-links{position:absolute;left:132px;top:19px}
.copyright{position:absolute;left:132px;top:46px}
.social{position:absolute;left:819px;top:34px;display:flex;align-items:center;gap:0}
.social span.dot{width:10px;height:10px;border-radius:50%;background:var(--navy);margin-left:22px}
.social span.dot:first-of-type{margin-left:10px}
.code{position:absolute;left:1116px;top:36px;font-size:11px}
</style>
</head>
<body>
<header class="site-header">
  <div class="brand"><div class="brand-square"></div><span class="brand-name">NORVANE</span></div>
  <div class="search">Search...
    <svg width="11" height="11" viewBox="0 0 12 12"><circle cx="5" cy="5" r="3.8" fill="none" stroke="#9aa1ab" stroke-width="1.6"/><line x1="8" y1="8" x2="11" y2="11" stroke="#9aa1ab" stroke-width="1.8"/></svg>
  </div>
  <div class="login">Log in</div>
</header>
<div class="header-rule"></div>

<section class="hero">
  <div class="hero-shade" role="img" aria-label="Blurred photograph of a retail store interior with clothing displays"></div>
</section>

<nav class="menu">
  <div class="menu-item">
    <div class="menu-icon"><svg width="34" height="34" viewBox="0 0 34 34"><rect x="1" y="1" width="32" height="32" fill="#fff"/></svg></div>
    <div class="menu-label">About Norvane</div>
  </div>
  <div class="menu-item">
    <div class="menu-icon"><svg width="36" height="38" viewBox="0 0 36 38"><circle cx="18" cy="9" r="8" fill="#fff"/><text x="18" y="13.5" font-size="12" font-weight="700" text-anchor="middle" fill="#0b2f6b" font-family="Lato,sans-serif">$</text><rect x="1" y="22" width="6" height="15" fill="#fff"/><rect x="10" y="19" width="6" height="18" fill="#fff"/><rect x="19" y="19" width="6" height="18" fill="#fff"/><rect x="28" y="22" width="6" height="15" fill="#fff"/></svg></div>
    <div class="menu-label">Our Approach<br>and Philosophy</div>
  </div>
  <div class="menu-item">
    <div class="menu-icon"><svg width="26" height="26" viewBox="0 0 26 26"><path d="M3 19 L17 5 L21 9 L7 23 L2 24 Z" fill="#fff"/><path d="M18.5 3.5 L20.5 1.5 L24.5 5.5 L22.5 7.5 Z" fill="#fff"/></svg></div>
    <div class="menu-label">Contact Us</div>
  </div>
</nav>

<section class="intro">
  <h1>Norvane Investment Management was founded in 2016 with a clear vision to create an independent and nimble firm focused on generating superior risk-adjusted returns.</h1>
  <p>Norvane has designed an innovative investment approach which aims to harness the best elements of alternative investment management whilst reducing its recognised shortcomings. We are a performance and client focused firm, committed to building lasting relationships, treating our clients like partners rather than revenue streams.</p>
</section>

<footer class="site-footer">
  <div class="footer-links">Disclaimer &nbsp;|&nbsp; Terms and Conditions | &nbsp;Stewardship | &nbsp;Pillar III</div>
  <div class="copyright">Copyrights © norvanim . 2017 | Allrights Reserved.</div>
  <div class="social">Connect With Us :<span class="dot"></span><span class="dot"></span><span class="dot"></span><span class="dot"></span><span class="dot"></span></div>
  <div class="code">C11</div>
</footer>
</body>
</html>
```